New Business Card Design Project

Need a design that will create an impact / strong impression towards our clients for our business. We are in the lighting business and we do lighting retrofits for large commercial to industrial clientele.

Target Market(s)

Lighting Industry

Industry/Entity Type

Business

Font styles to use
Other font styles liked:
• we would like to use the font on our logo, not sure what it is though..

Requirements
Must have
• Our logo.
Nice to have
• We are open to suggestions that have to do with lighting.

```html
<!DOCTYPE html>
<html lang="en">
<head>
<meta charset="utf-8">
<title>Brightline Retrofit Group – Business Card</title>
<link rel="stylesheet" href="https://fonts.googleapis.com/css2?family=Lato:wght@400;700&family=Oswald:wght@700&display=swap">
<style>
  :root {
    --backdrop: #3a3a3c;
    --brand-green: #0a833a;
    --paper: #ffffff;
    --ink: #1a1a1a;
  }
  html, body {
    margin: 0;
    padding: 0;
    width: 1200px;
    height: 900px;
    overflow: hidden;
    background: var(--backdrop);
  }
  .canvas {
    position: relative;
    width: 1200px;
    height: 900px;
  }
  .card {
    position: absolute;
    left: 280px;
    width: 640px;
    height: 366px;
    box-sizing: border-box;
    overflow: hidden;
  }
  /* Front */
  .card-front {
    top: 60px;
    background: var(--brand-green);
    color: var(--paper);
    font-family: "Lato", sans-serif;
  }
  .wordmark {
    position: absolute;
    top: 118px;
    left: 0;
    right: 0;
    display: flex;
    justify-content: center;
    align-items: center;
    gap: 14px;
  }
  .wordmark-dot {
    width: 22px;
    height: 22px;
    border-radius: 50%;
    background: var(--paper);
  }
  .wordmark-name {
    font-weight: 700;
    font-size: 30px;
    letter-spacing: 1.5px;
    text-transform: uppercase;
    line-height: 1.15;
    color: var(--paper);
  }
  .front-web {
    position: absolute;
    bottom: 52px;
    left: 0;
    right: 0;
    text-align: center;
    font-size: 17px;
    letter-spacing: 1px;
  }
  /* Back */
  .card-back {
    top: 474px;
    background: var(--paper);
    color: var(--ink);
    font-family: "Lato", sans-serif;
    border-bottom: 9px solid var(--brand-green);
  }
  .identity {
    position: absolute;
    top: 120px;
    left: 40px;
    width: 264px;
    text-align: right;
  }
  .person-name {
    margin: 0;
    font-family: "Oswald", sans-serif;
    font-weight: 700;
    font-size: 40px;
    line-height: 1.05;
    color: var(--brand-green);
    text-transform: uppercase;
    letter-spacing: 0.5px;
  }
  .person-role {
    margin: 4px 0 0;
    font-size: 18px;
  }
  .divider {
    position: absolute;
    left: 330px;
    top: 118px;
    width: 2px;
    height: 112px;
    background: var(--brand-green);
  }
  .contacts {
    position: absolute;
    left: 356px;
    top: 122px;
    margin: 0;
    padding: 0;
    list-style: none;
    font-size: 17px;
  }
  .contacts li {
    display: flex;
    align-items: center;
    gap: 12px;
    height: 27px;
  }
  .contacts svg {
    width: 16px;
    height: 16px;
    fill: var(--brand-green);
    flex: none;
  }
  .address {
    position: absolute;
    left: 0;
    right: 0;
    bottom: 32px;
    text-align: center;
    font-size: 19px;
  }
</style>
</head>
<body>
<main class="canvas">
  <section class="card card-front" aria-label="Card front">
    <div class="wordmark">
      <span class="wordmark-dot" aria-hidden="true"></span>
      <span class="wordmark-name">Brightline Retrofit<br>Group, LLC</span>
    </div>
    <div class="front-web">www.brightline-retro.com</div>
  </section>

  <section class="card card-back" aria-label="Card back">
    <div class="identity">
      <h1 class="person-name">Mark Ellison</h1>
      <p class="person-role">Manager</p>
    </div>
    <div class="divider"></div>
    <ul class="contacts">
      <li>
        <svg viewBox="0 0 16 16" aria-hidden="true"><path d="M3.5 1.5l2.5 0 1 3.5-1.8 1.2a8 8 0 0 0 4.6 4.6L11 9l3.5 1v2.5c0 1-1 2-2 2A11 11 0 0 1 1.5 3.5c0-1 1-2 2-2z"/></svg>
        <span>(555) 014-2300</span>
      </li>
      <li>
        <svg viewBox="0 0 16 16" aria-hidden="true"><rect x="4" y="1" width="8" height="4"/><rect x="1" y="6" width="14" height="6" rx="1"/><rect x="4" y="10" width="8" height="5" fill="#fff" stroke="#0a833a" stroke-width="1.5"/></svg>
        <span>(555) 014-2301</span>
      </li>
      <li>
        <svg viewBox="0 0 16 16" aria-hidden="true"><rect x="1" y="3" width="14" height="10"/><path d="M1 3l7 6 7-6" fill="none" stroke="#fff" stroke-width="1.4"/></svg>
        <span>info@brightline-retro.com</span>
      </li>
      <li>
        <svg viewBox="0 0 16 16" aria-hidden="true"><circle cx="8" cy="8" r="7"/><g fill="none" stroke="#fff" stroke-width="1"><ellipse cx="8" cy="8" rx="3" ry="7"/><path d="M1 8h14M2.5 4.5h11M2.5 11.5h11"/></g></svg>
        <span>www.brightline-retro.com</span>
      </li>
    </ul>
    <div class="address">4210 Harbor Lane, Riverton, IL 60999</div>
  </section>
</main>
</body>
</html>
```